Business Card Design

Harbor Bin 264 is a waste collection business contracted to remove waste from city streets, parks and caravan parks.

Target Market(s)

CEO and Managing Directors

Industry/Entity Type

Business

Contact Information for Business Card

Harbor Bin 264
Manager
Glen Haskett
0437915260
harborbin264@quillmail.com.au

Colors
33a6d7
ecf7fb

Requirements
Must have
• Must have eye catching design that stands out above others ( tender process can be very competitive ).
Nice to have
• A garbage truck on or in the logo somehow

```html
<!DOCTYPE html>
<html lang="en">
<head>
<meta charset="utf-8">
<title>Harbor Bin 264 – Business Card</title>
<link href="https://fonts.googleapis.com/css2?family=Poppins:wght@500;600&family=Roboto:wght@500;700&display=swap" rel="stylesheet">
<style>
  :root {
    --backdrop: #3b3836;
    --card-white: #ffffff;
    --card-tint: #ecf7fb;
    --brand-yellow: #f9d114;
    --brand-blue: #33a6d7;
    --ink: #111111;
    --on-blue: #ffffff;
    --truck-orange: #f08a1c;
    --truck-light: #f5b56c;
  }
  * { margin: 0; padding: 0; box-sizing: border-box; }
  html, body {
    width: 1200px;
    height: 720px;
    overflow: hidden;
    background: var(--backdrop);
  }
  .card {
    position: absolute;
    left: 40px;
    top: 33px;
    width: 1120px;
    height: 654px;
    background: radial-gradient(circle at 30% 40%, var(--card-white) 0%, var(--card-tint) 100%);
    overflow: hidden;
  }
  .card-shapes {
    position: absolute;
    inset: 0;
    width: 100%;
    height: 100%;
  }
  .shape-yellow { fill: var(--brand-yellow); }
  .shape-blue { fill: var(--brand-blue); }

  .truck-visual {
    position: absolute;
    left: 110px;
    top: 70px;
    width: 388px;
    height: 300px;
    border-radius: 50%;
    background: radial-gradient(ellipse at 55% 45%, var(--truck-orange) 0%, var(--truck-light) 50%, transparent 72%);
  }

  .brand-name {
    position: absolute;
    left: 110px;
    top: 385px;
    width: 388px;
    text-align: center;
    font-family: "Poppins", sans-serif;
    font-weight: 600;
    font-size: 46px;
    line-height: 1.15;
    color: var(--ink);
  }

  .holder {
    position: absolute;
    right: 60px;
    top: 112px;
    text-align: right;
    font-family: "Roboto", sans-serif;
    color: var(--ink);
  }
  .holder-name { font-size: 40px; font-weight: 700; line-height: 1.1; }
  .holder-title { font-size: 26px; font-weight: 500; margin-top: 4px; }

  .contact-list {
    position: absolute;
    right: 46px;
    top: 382px;
    list-style: none;
    font-family: "Poppins", sans-serif;
    font-weight: 500;
    font-size: 26px;
    color: var(--on-blue);
  }
  .contact-item {
    display: flex;
    justify-content: flex-end;
    align-items: center;
    gap: 16px;
    height: 52px;
    margin-bottom: 30px;
  }
  .contact-icon {
    width: 30px;
    height: 30px;
    fill: none;
    stroke: var(--on-blue);
    stroke-width: 2.4;
    stroke-linecap: round;
    stroke-linejoin: round;
  }
</style>
</head>
<body>
  <main class="card">
    <svg class="card-shapes" viewBox="0 0 1120 654" aria-hidden="true">
      <polygon class="shape-yellow" points="472,0 1120,0 1120,321 668,321"/>
      <polygon class="shape-blue" points="668,333 1120,333 1120,654 473,654"/>
    </svg>

    <div class="truck-visual" role="img" aria-label="Orange garbage truck tipping waste from its raised rear bin"></div>

    <div class="brand-name">Harbor Bin<br>264</div>

    <div class="holder">
      <p class="holder-name">Glen Haskett</p>
      <p class="holder-title">Manager</p>
    </div>

    <ul class="contact-list">
      <li class="contact-item">
        <span>0437915260</span>
        <svg class="contact-icon" viewBox="0 0 24 24" aria-hidden="true">
          <path d="M5 3h4l2 5-2.5 1.5a11 11 0 0 0 6 6L16 13l5 2v4a2 2 0 0 1-2 2A16 16 0 0 1 3 5a2 2 0 0 1 2-2z"/>
        </svg>
      </li>
      <li class="contact-item">
        <span>harborbin264@quillmail.com.au</span>
        <svg class="contact-icon" viewBox="0 0 24 24" aria-hidden="true">
          <rect x="2" y="5" width="20" height="14" rx="1"/>
          <path d="M2 6l10 7 10-7M2 19l7-6M22 19l-7-6"/>
        </svg>
      </li>
    </ul>
  </main>
</body>
</html>
```